Detail Shop Business card design

i need a business card design for my new detailing company called 'Brisk's Polish Works'. i want an all black and white design . simple, direct and to the point. i want the designer to choose a fitting font to match the logothe front should have logo, address, phone and email and the back side should have a slogan and text indicating that we offer services on anything including cars, trucks, motorcycles and RVs. slogan will read "we take pride in your ride"
maybe also very small on the back side the IG icon with Brisks_Polish_Works

phone 208.417.6352
address 3847 E Larkin Ave
Spokane WA 99214
email: BrisksPolish@mailvexo.com

Target Market(s)

all ages , auto enthusiasts

Industry/Entity Type

Automotive

Contact Information for Business Card

the front should have logo, address, phone and email and the back side should have a slogan and text indicating that we offer services on anything including cars, trucks, motorcycles and RVs. slogan will read "we take pride in your ride"

phone 208.417.6352
address 3847 E Larkin Ave
Spokane WA 99214

Colors
000000
ffffff

Requirements
Must have
• bold font and very simple design with good spacing
Nice to have
• anything creative from the designer indicating we service any types of vehicles
Should not have
• any colors ,

```html
<!DOCTYPE html>
<html lang="en">
<head>
<meta charset="utf-8">
<title>Brisk's Polish Works – Business Card</title>
<link rel="stylesheet" href="https://fonts.googleapis.com/css2?family=Roboto+Slab:wght@400;700&display=swap">
<style>
  :root {
    --ink: #000000;
    --paper: #ffffff;
    --backdrop: #1c1c1c;
  }
  html, body {
    margin: 0;
    padding: 0;
    width: 1200px;
    height: 900px;
    overflow: hidden;
    background: var(--backdrop);
    font-family: "Roboto Slab", Georgia, serif;
    color: var(--ink);
  }
  .sheet {
    position: relative;
    width: 1200px;
    height: 900px;
  }
  .card {
    position: absolute;
    left: 250px;
    width: 700px;
    height: 400px;
    background: var(--paper);
    overflow: hidden;
  }
  .card--back { top: 35px; }
  .card--front { top: 465px; }

  .rule {
    position: absolute;
    left: 0;
    right: 0;
    background: var(--ink);
  }
  .card--back .rule--a { top: 18px; height: 6px; }
  .card--back .rule--b { top: 34px; height: 2px; }
  .card--back .rule--c { bottom: 38px; height: 2px; }
  .card--back .rule--d { bottom: 0; height: 24px; }
  .card--front .rule--a { top: 0; height: 22px; }
  .card--front .rule--b { top: 36px; height: 2px; }
  .card--front .rule--c { bottom: 36px; height: 2px; }
  .card--front .rule--d { bottom: 18px; height: 6px; }

  .brand {
    display: flex;
    flex-direction: column;
    align-items: center;
    text-align: center;
  }
  .brand__mark {
    display: flex;
    align-items: center;
    gap: 10px;
  }
  .brand__dot {
    width: 22px;
    height: 22px;
    border-radius: 50%;
    background: var(--ink);
  }
  .brand__name {
    font-weight: 700;
    font-size: 34px;
    letter-spacing: 0.5px;
    margin: 0;
  }
  .brand__slogan {
    font-weight: 700;
    font-size: 17px;
    margin: 14px 0 0;
  }
  .card--back .brand {
    position: absolute;
    left: 0;
    right: 0;
    top: 118px;
  }
  .social {
    display: flex;
    align-items: center;
    gap: 7px;
    margin-top: 12px;
    font-size: 12px;
  }
  .social__dot {
    width: 12px;
    height: 12px;
    border: 1.5px solid var(--ink);
    border-radius: 50%;
    box-sizing: border-box;
  }

  .card--front .brand {
    position: absolute;
    left: 70px;
    top: 160px;
    align-items: flex-start;
    text-align: left;
  }
  .card--front .brand__name { font-size: 30px; }

  .contact {
    position: absolute;
    right: 40px;
    top: 120px;
    list-style: none;
    margin: 0;
    padding: 0;
    font-size: 14px;
    line-height: 1.35;
  }
  .contact__item {
    display: flex;
    align-items: flex-start;
    gap: 12px;
    margin-bottom: 6px;
  }
  .contact__icon {
    width: 14px;
    height: 14px;
    flex: none;
    margin-top: 2px;
  }
</style>
</head>
<body>
<main class="sheet">

  <section class="card card--back" aria-label="Card back">
    <div class="rule rule--a"></div>
    <div class="rule rule--b"></div>
    <div class="brand">
      <div class="brand__mark">
        <span class="brand__dot"></span>
        <h1 class="brand__name">Brisk's Polish Works</h1>
      </div>
      <p class="brand__slogan">We Take Pride In Your Ride</p>
      <div class="social">
        <span class="social__dot"></span>
        <span class="social__handle">Brisks_Polish_Works</span>
      </div>
    </div>
    <div class="rule rule--c"></div>
    <div class="rule rule--d"></div>
  </section>

  <section class="card card--front" aria-label="Card front">
    <div class="rule rule--a"></div>
    <div class="rule rule--b"></div>
    <div class="brand">
      <div class="brand__mark">
        <span class="brand__dot"></span>
        <h2 class="brand__name">Brisk's Polish Works</h2>
      </div>
      <p class="brand__slogan">We Take Pride In Your Ride</p>
    </div>
    <ul class="contact">
      <li class="contact__item">
        <svg class="contact__icon" viewBox="0 0 16 16" aria-hidden="true">
          <path d="M3 2h3l1.5 3.5-2 1.3a8 8 0 0 0 3.7 3.7l1.3-2L14 10v3a1 1 0 0 1-1 1A11 11 0 0 1 2 3a1 1 0 0 1 1-1z" fill="#000"/>
        </svg>
        <span>208.417.6352</span>
      </li>
      <li class="contact__item">
        <svg class="contact__icon" viewBox="0 0 16 16" aria-hidden="true">
          <path d="M15 1 1 7l5.5 2.5L9 15z" fill="#000"/>
        </svg>
        <span>BrisksPolish@mailvexo.com</span>
      </li>
      <li class="contact__item">
        <svg class="contact__icon" viewBox="0 0 16 16" aria-hidden="true">
          <path d="M8 1a5 5 0 0 0-5 5c0 4 5 9 5 9s5-5 5-9a5 5 0 0 0-5-5zm0 7a2 2 0 1 1 0-4 2 2 0 0 1 0 4z" fill="#000"/>
        </svg>
        <span>3847 E Larkin Ave<br>Spokane WA 99214</span>
      </li>
    </ul>
    <div class="rule rule--c"></div>
    <div class="rule rule--d"></div>
  </section>

</main>
</body>
</html>
```